Corvane Paintless Dent Removal

Our company works on vehicles removing dents using a highly skilled trade which the metal is massaged out with special tools without disturbing the original paint, hence paintless dent removal. Besides keeping the paint and metal original its also very environmentally friendly since no paint or toxic fillers are used. Also we we are one of the most experienced companies in the business with 25 years

Target Market(s)

Retail Automobile consumers, Auto Dealerships and Auto Body Shops

Industry/Entity Type

Auto Repair

Contact Information for Business Card

Dale Hollister
PO Box 518 Brookmere, NY 11962
631-555-0148
corvanepdr@mailbox-example.com
website corvanepdr.example
youtube corvane paintless dent removal
25 years of experience removing Dents, Dings and Hail Damage

Font styles to use
Serif
Sans Serif

Colors

Designer to choose colors to be used in the design.

Requirements
Must have
• I do like things that are simple but classy and somewhat bold, also I like my logo so that should be somewhat important

```html
<!DOCTYPE html>
<html lang="en">
<head>
<meta charset="utf-8">
<title>Corvane Paintless Dent Removal — Business Card</title>
<link href="https://fonts.googleapis.com/css2?family=Roboto+Condensed:wght@400;700&display=swap" rel="stylesheet">
<style>
  :root {
    --navy: #14305a;
    --green: #7ec21c;
    --paper: #ffffff;
    --stage: #e9e6e1;
    --badge: #1d1d1d;
    --ink-light: #ffffff;
    --ink-muted: #8a8a8a;
  }
  * { box-sizing: border-box; margin: 0; padding: 0; }
  html, body {
    width: 1200px; height: 886px; overflow: hidden;
    background: var(--stage);
    font-family: "Roboto Condensed", Arial, sans-serif;
  }
  .stage {
    width: 1200px; height: 886px;
    display: flex; align-items: center; justify-content: center; gap: 40px;
  }
  .card {
    position: relative;
    width: 540px; height: 309px;
    background: var(--paper);
    box-shadow: 0 6px 18px rgba(0,0,0,.18);
    overflow: hidden;
  }
  .wordmark {
    font-weight: 700;
    color: var(--navy);
    text-align: center;
    line-height: 1.05;
    text-transform: uppercase;
  }
  .wordmark .name { display: block; letter-spacing: 1px; }
  .wordmark .trade { display: block; text-transform: none; font-size: .42em; letter-spacing: .5px; }

  /* front */
  .front .wordmark {
    position: absolute; left: 0; right: 0; top: 52px;
    font-size: 40px;
  }
  .years-badge {
    position: absolute; top: 16px; right: 18px;
    width: 46px; height: 46px; border-radius: 50%;
    background: var(--badge);
    border: 3px solid #c9a24a;
  }
  .band-person {
    position: absolute; left: 0; bottom: 0;
    width: 52%; height: 112px;
    background: var(--navy);
    color: var(--ink-light);
    padding: 22px 0 0 34px;
  }
  .band-person .person { font-size: 21px; font-weight: 700; text-transform: uppercase; letter-spacing: .3px; }
  .band-person .address { font-size: 15px; line-height: 1.35; margin-top: 4px; }
  .band-contact {
    position: absolute; right: 0; bottom: 0;
    width: 48%; height: 150px;
    background: var(--green);
    color: var(--ink-light);
    padding: 26px 22px 0 22px;
    display: flex; flex-direction: column; gap: 8px;
    align-items: flex-end;
  }
  .contact-line { display: flex; align-items: center; gap: 8px; font-size: 14px; }
  .contact-line svg { width: 13px; height: 13px; flex: none; }

  /* back */
  .back .wordmark {
    position: absolute; left: 0; right: 0; top: 100px;
    font-size: 48px;
  }
  .back .web {
    position: absolute; left: 0; right: 0; bottom: 46px;
    text-align: center; font-size: 13px; letter-spacing: 6px;
    color: var(--ink-muted);
  }
</style>
</head>
<body>
<main class="stage">
  <section class="card front" aria-label="Business card front">
    <div class="wordmark"><span class="name">Corvane</span><span class="trade">Paintless Dent Removal</span></div>
    <div class="years-badge" role="img" aria-label="25 years of experience badge"></div>
    <div class="band-person">
      <p class="person">Dale Hollister</p>
      <p class="address">PO Box 518<br>Brookmere, NY 11962</p>
    </div>
    <div class="band-contact">
      <p class="contact-line">631-555-0148
        <svg viewBox="0 0 16 16" aria-hidden="true"><path fill="#fff" d="M3.5 1.5l2.5 2.6-1.4 1.8c.9 2 2.6 3.7 4.6 4.6l1.8-1.4 2.6 2.5-1.5 2.3C6.6 14 2 9.4 1.5 3z"/></svg></p>
      <p class="contact-line">corvanepdr@mailbox-example.com
        <svg viewBox="0 0 16 16" aria-hidden="true"><rect x="1" y="3" width="14" height="10" fill="#fff"/><path d="M1 3l7 6 7-6" stroke="#7ec21c" stroke-width="1.4" fill="none"/></svg></p>
      <p class="contact-line">corvane paintless dent removal
        <svg viewBox="0 0 16 16" aria-hidden="true"><rect x="1" y="3" width="14" height="10" fill="#fff"/></svg></p>
    </div>
  </section>

  <section class="card back" aria-label="Business card back">
    <div class="wordmark"><span class="name">Corvane</span><span class="trade">Paintless Dent Removal</span></div>
    <p class="web">www.corvanepdr.example</p>
  </section>
</main>
</body>
</html>
```